Thornbury Cafe Business Card

We are a café in Sydney.
see website for details. http://www.thornburycafe.com.au

want a single sided business card - no person's name on there.
This is to hand out to customers
use the attached logo

Industry/Entity Type

Business

Contact Information for Business Card

Thornbury Café
Mezzanine Level,
517-521 Kelvin St
Sydney NSW 2000
T: 9418 5063
W: www.thornburycafe.com.au
F: facebook.com/ThornburyCafeSydney

Catering Available
Phone for Lunchtime Bookings

```html
<!DOCTYPE html>
<html lang="en">
<head>
<meta charset="utf-8">
<title>Thornbury Cafe Business Card</title>
<link href="https://fonts.googleapis.com/css2?family=Quicksand:wght@500;700&display=swap" rel="stylesheet">
<style>
  :root {
    --backdrop: #e6e3de;
    --card-light: #4b586b;
    --card-dark: #2c3542;
    --ink: #eef0f3;
    --ink-soft: #d7dbe1;
    --accent: #b35a2a;
    --icon-fill: #f4f5f7;
    --icon-ink: #2f3846;
  }
  * { margin: 0; padding: 0; box-sizing: border-box; }
  html, body {
    width: 1200px;
    height: 837px;
    overflow: hidden;
    background: var(--backdrop);
    font-family: "Quicksand", sans-serif;
  }
  .canvas {
    width: 1200px;
    height: 837px;
    display: flex;
    align-items: center;
    justify-content: center;
  }
  .business-card {
    position: relative;
    width: 1000px;
    height: 611px;
    background: radial-gradient(ellipse at 40% 30%, var(--card-light) 0%, var(--card-dark) 85%);
    box-shadow: 0 10px 30px rgba(0,0,0,0.25);
    color: var(--ink);
  }
  .brand {
    position: absolute;
    left: 70px;
    top: 250px;
    display: flex;
    align-items: center;
    gap: 22px;
  }
  .brand-dot {
    width: 64px;
    height: 64px;
    border-radius: 50%;
    background: var(--accent);
    flex: none;
  }
  .brand-name {
    font-size: 64px;
    font-weight: 700;
    letter-spacing: 1px;
    color: var(--ink);
  }
  .contact-list {
    position: absolute;
    right: 40px;
    list-style: none;
    text-align: right;
    font-weight: 500;
    letter-spacing: 1.5px;
    color: var(--ink-soft);
  }
  .contact-list li {
    display: flex;
    justify-content: flex-end;
    align-items: center;
    gap: 10px;
    font-size: 24px;
    line-height: 34px;
  }
  .address { top: 50px; }
  .online { bottom: 40px; }
  .online .heading {
    font-weight: 700;
    font-size: 26px;
    color: var(--ink);
    margin-bottom: 2px;
  }
  .icon-slot { width: 20px; height: 20px; flex: none; }
  .icon-spacer { width: 20px; flex: none; }
</style>
</head>
<body>
<main class="canvas">
  <article class="business-card">
    <div class="brand">
      <span class="brand-dot"></span>
      <span class="brand-name">Thornbury Cafe</span>
    </div>

    <ul class="contact-list address">
      <li>517-521 Kelvin St, Sydney
        <svg class="icon-slot" viewBox="0 0 20 20" aria-label="location">
          <circle cx="10" cy="10" r="10" fill="var(--icon-fill)"/>
          <path d="M10 4a4 4 0 0 0-4 4c0 3 4 8 4 8s4-5 4-8a4 4 0 0 0-4-4z" fill="var(--icon-ink)"/>
          <circle cx="10" cy="8" r="1.6" fill="var(--icon-fill)"/>
        </svg>
      </li>
      <li>Mezzanine level<span class="icon-spacer"></span></li>
      <li>+612 9418 5063
        <svg class="icon-slot" viewBox="0 0 20 20" aria-label="phone">
          <circle cx="10" cy="10" r="10" fill="var(--icon-fill)"/>
          <path d="M7 5l2 2.5-1.2 1.3a7 7 0 0 0 3.4 3.4L12.5 11 15 13l-1.2 1.6c-4.5-.5-8.1-4.1-8.4-8.4z" fill="var(--icon-ink)"/>
        </svg>
      </li>
    </ul>

    <ul class="contact-list online">
      <li class="heading">Order online:<span class="icon-spacer"></span></li>
      <li>www.thornburycafe.com.au
        <svg class="icon-slot" viewBox="0 0 20 20" aria-label="website">
          <circle cx="10" cy="10" r="10" fill="var(--icon-fill)"/>
        </svg>
      </li>
      <li>chatterpage.com/thornburycafesydney
        <svg class="icon-slot" viewBox="0 0 20 20" aria-label="social page">
          <circle cx="10" cy="10" r="10" fill="var(--icon-fill)"/>
        </svg>
      </li>
    </ul>
  </article>
</main>
</body>
</html>
```